need corporate, modern business card created for Consulting Company

I need a slick business card using elements from my website, as well as, integrating my pixelforge-created logo (see files).

The business card needs to be:
1. Corporate and modern
2. Clean and professional

I've included a PSD with the logo/icon that you can use to create it. Feel free to try a metallic finish on the logo, make it bigger/small, underlay it. Whatever you need to do to make my card stand out.

Try a black background, or white background or gray.

The idea is for my card to be memorable as well as professional and corporate.

Target Market(s)

Corporate business in the US and Canada.

Industry/Entity Type

Business

Contact Information for Business Card

Commerce Advancing Methods
Martin Coles, Senior Partner
office: 1 877 555 0143
mobile: 1 519 555 0172
website: http://www.brightvale.example

Requirements
Must have
• Card-related information
• corporate, yet modern
• clean and professional
• incorporate the icon only
• must have an editable form when complete!
Nice to have
• metallic icon might be cool
• try it with white or black

```html
<!DOCTYPE html>
<html lang="en">
<head>
<meta charset="utf-8">
<title>Brightvale Business Card</title>
<link rel="stylesheet" href="https://fonts.googleapis.com/css2?family=Open+Sans:wght@400;600;700&display=swap">
<style>
  :root {
    --canvas-bg: #e6e4e0;
    --card-dark: #262628;
    --card-light: #f7f7f7;
    --brand-blue: #3d8fd6;
    --ink: #1e1e1e;
    --ink-soft: #3a3a3a;
    --muted: #6b6b6b;
    --line-light: #d9d9d9;
  }
  * { box-sizing: border-box; margin: 0; padding: 0; }
  html, body { width: 1200px; height: 885px; overflow: hidden; }
  body {
    background: var(--canvas-bg);
    font-family: "Open Sans", Arial, sans-serif;
    position: relative;
  }
  .card {
    position: absolute;
    left: 320px;
    width: 560px;
    height: 320px;
    border-radius: 22px;
    box-shadow: 0 6px 18px rgba(0,0,0,.18);
    overflow: hidden;
  }
  /* Front */
  .card--front { top: 100px; background: var(--card-dark); }
  .front-brand {
    position: absolute; left: 0; right: 0; top: 92px;
    display: flex; align-items: center; justify-content: center; gap: 18px;
  }
  .brand-square {
    width: 46px; height: 46px; border-radius: 6px; background: var(--brand-blue);
  }
  .front-brand .brand-name {
    font-weight: 700; font-size: 66px; letter-spacing: -1px; color: #ffffff; line-height: 1;
  }
  .front-web {
    position: absolute; left: 40px; right: 40px; top: 214px;
    display: flex; align-items: center; gap: 16px;
  }
  .front-web .rule { flex: 1; height: 1px; background: rgba(255,255,255,.7); }
  .front-web .url { color: var(--brand-blue); font-size: 19px; font-weight: 600; }

  /* Back */
  .card--back { top: 470px; background: linear-gradient(135deg, #ffffff 0%, var(--card-light) 60%, #e9e9e9 100%); }
  .back-brand { position: absolute; left: 40px; top: 32px; }
  .back-brand .logo-row { display: flex; align-items: center; gap: 12px; }
  .back-brand .brand-square { width: 30px; height: 30px; border-radius: 4px; }
  .back-brand .brand-name {
    font-weight: 700; font-size: 42px; color: var(--brand-blue); letter-spacing: -0.5px; line-height: 1;
  }
  .back-brand .tagline { margin-top: 6px; margin-left: 42px; font-size: 14px; color: var(--ink-soft); }
  .back-rule {
    position: absolute; left: 40px; right: 40px; top: 128px; height: 1px; background: var(--brand-blue);
  }
  .person { position: absolute; left: 40px; top: 148px; }
  .person .name { font-size: 26px; font-weight: 600; color: var(--ink); line-height: 1.1; }
  .person .title { font-size: 18px; color: var(--brand-blue); margin-top: 2px; }
  .person .address { margin-top: 14px; font-size: 13.5px; color: var(--ink-soft); line-height: 1.55; }
  .contacts { position: absolute; left: 318px; top: 162px; list-style: none; }
  .contacts li {
    display: flex; align-items: center; gap: 10px;
    font-size: 14px; color: var(--ink-soft); height: 28px;
  }
  .contacts .icon {
    width: 19px; height: 19px; border-radius: 3px; background: var(--brand-blue);
    display: flex; align-items: center; justify-content: center;
  }
  .contacts svg { width: 13px; height: 13px; }
</style>
</head>
<body>

<section class="card card--front" aria-label="Card front">
  <div class="front-brand">
    <span class="brand-square"></span>
    <span class="brand-name">brightvale</span>
  </div>
  <div class="front-web">
    <span class="rule"></span>
    <span class="url">www.brightvale.example</span>
    <span class="rule"></span>
  </div>
</section>

<section class="card card--back" aria-label="Card back">
  <div class="back-brand">
    <div class="logo-row">
      <span class="brand-square"></span>
      <span class="brand-name">brightvale</span>
    </div>
    <p class="tagline">Commerce Advancing Methods</p>
  </div>
  <div class="back-rule"></div>

  <div class="person">
    <p class="name">Martin Coles</p>
    <p class="title">Senior Partner</p>
    <p class="address">48 Harbour Lane, Suite 610<br>Toronto, Ontario, M5J 0A1</p>
  </div>

  <ul class="contacts">
    <li>
      <span class="icon"><svg viewBox="0 0 16 16" fill="#fff"><path d="M4 1.5l2.2 2.8-1.3 1.6c.9 2 2.4 3.5 4.2 4.4l1.6-1.3 2.8 2.2-1.4 2.3C7 13.2 2.8 9 1.7 3z"/></svg></span>
      1 877 555 0143
    </li>
    <li>
      <span class="icon"><svg viewBox="0 0 16 16" fill="none" stroke="#fff" stroke-width="1.6"><rect x="4.5" y="1.5" width="7" height="13" rx="1.2"/><line x1="7" y1="12" x2="9" y2="12"/></svg></span>
      1 519 555 0172
    </li>
    <li>
      <span class="icon"><svg viewBox="0 0 16 16" fill="none" stroke="#fff" stroke-width="1.5"><rect x="1.5" y="3.5" width="13" height="9"/><path d="M1.5 3.5L8 9l6.5-5.5"/></svg></span>
      info@brightvale.example
    </li>
    <li>
      <span class="icon"><svg viewBox="0 0 16 16" fill="none" stroke="#fff" stroke-width="1.4"><circle cx="8" cy="8" r="6"/><ellipse cx="8" cy="8" rx="2.6" ry="6"/><line x1="2" y1="8" x2="14" y2="8"/></svg></span>
      www.brightvale.example
    </li>
  </ul>
</section>

</body>
</html>
```